Ward Compass Business Card Design*

We need a business card design for our company Ward Compass. Our company is specialized in providing online consulting services regarding medical institutions, hospitals and doctors. We work with patients worldwide looking to choose between healthcare providers. We have a website you may use as a reference, where we list doctors and clinics worldwide. So we target Medical providers as well as patients worldwide.
Target Market(s)
Medical Providers and patients around the world
Industry/Entity Type
Medical
Contact Information for Business Card
Salwa Kettani
CEO
+90 612 348 2175
info@wardcompass.example
www.wardcompass.example
14 Annakhil 7 H.R.B. Rabat, Morocco
Requirements
Must have
- Company logo/name on one full side, personal info and smaller logo and company name on the other side.
Nice to have
- Smart and elegant design

```html
<!DOCTYPE html>
<html lang="en">
<head>
<meta charset="utf-8">
<title>Ward Compass – Business Card</title>
<link href="https://fonts.googleapis.com/css2?family=Open+Sans:wght@400;700&display=swap" rel="stylesheet">
<style>
  :root {
    --backdrop: #e6e6e6;
    --card-grey: #6f6f6f;
    --card-white: #ffffff;
    --navy: #1d3f6e;
    --text-light: #ffffff;
  }
  * { margin: 0; padding: 0; box-sizing: border-box; }
  html, body { width: 1200px; height: 768px; overflow: hidden; }
  body {
    background: var(--backdrop);
    font-family: "Open Sans", Arial, sans-serif;
    display: flex;
    align-items: center;
    justify-content: center;
    gap: 40px;
  }
  .card {
    position: relative;
    width: 540px;
    height: 309px;
    background: var(--card-grey);
    overflow: hidden;
    box-shadow: 0 6px 18px rgba(0,0,0,0.18);
  }
  /* Back side */
  .card-back .brand {
    position: absolute;
    top: 96px; left: 0; right: 0;
    display: flex;
    align-items: center;
    justify-content: center;
    gap: 14px;
  }
  .card-back .brand-dot {
    width: 46px; height: 46px;
    border: 7px solid var(--text-light);
    border-radius: 50%;
  }
  .card-back .brand-name {
    color: var(--text-light);
    font-size: 26px;
    font-weight: 400;
    letter-spacing: 2px;
    text-transform: uppercase;
  }
  .card-back .web {
    position: absolute;
    bottom: 58px; left: 0; right: 0;
    text-align: center;
    color: var(--text-light);
    font-size: 14px;
    letter-spacing: 6px;
  }
  /* Front side */
  .card-front .panel { position: absolute; inset: 0; }
  .card-front .brand {
    position: absolute;
    top: 140px; left: 28px;
    display: flex;
    align-items: center;
    gap: 9px;
  }
  .card-front .brand-dot {
    width: 26px; height: 26px;
    border: 5px solid var(--navy);
    border-radius: 50%;
  }
  .card-front .brand-name {
    color: var(--navy);
    font-size: 17px;
    font-weight: 400;
    letter-spacing: 1.3px;
    text-transform: uppercase;
  }
  .contact {
    position: absolute;
    right: 26px; top: 32px;
    text-align: right;
    color: var(--text-light);
  }
  .person-name { font-size: 18px; font-weight: 700; line-height: 1.1; }
  .person-role { font-size: 12px; margin-bottom: 50px; }
  .address { font-size: 12px; line-height: 1.35; margin-bottom: 12px; }
  .lines { list-style: none; font-size: 12px; line-height: 1.55; }
  .lines li { display: flex; align-items: center; justify-content: flex-end; gap: 9px; }
  .lines svg { width: 12px; height: 12px; fill: var(--text-light); }
</style>
</head>
<body>

<section class="card card-back" aria-label="Card back">
  <div class="brand">
    <span class="brand-dot"></span>
    <span class="brand-name">Ward Compass</span>
  </div>
  <p class="web">www.wardcompass.example</p>
</section>

<section class="card card-front" aria-label="Card front">
  <svg class="panel" viewBox="0 0 540 309" width="540" height="309">
    <circle cx="100" cy="154" r="170" fill="var(--card-white)"/>
    <path d="M 188 2 A 176 176 0 0 1 188 306" fill="none" stroke="var(--navy)" stroke-width="6"/>
  </svg>
  <div class="brand">
    <span class="brand-dot"></span>
    <span class="brand-name">Ward Compass</span>
  </div>
  <div class="contact">
    <p class="person-name">Salwa Kettani</p>
    <p class="person-role">CEO</p>
    <p class="address">14 Annakhil 7<br>H.R.B. Rabat, Morocco</p>
    <ul class="lines">
      <li>+90 612 348 2175
        <svg viewBox="0 0 16 16"><path d="M3 1h3l1 4-2 1c1 2 3 4 5 5l1-2 4 1v3c0 1-1 2-2 2C7 15 1 9 1 3c0-1 1-2 2-2z"/></svg></li>
      <li>info@wardcompass.example
        <svg viewBox="0 0 16 16"><path d="M1 3h14v10H1z M2 4l6 5 6-5" fill="none" stroke="#fff" stroke-width="1.5"/></svg></li>
      <li>www.wardcompass.example
        <svg viewBox="0 0 16 16"><circle cx="8" cy="8" r="6.5" fill="none" stroke="#fff" stroke-width="1.5"/><path d="M1.5 8h13M8 1.5c-3 4-3 9 0 13M8 1.5c3 4 3 9 0 13" fill="none" stroke="#fff" stroke-width="1"/></svg></li>
    </ul>
  </div>
</section>

</body>
</html>
```